Business Card Design Project

We have recently completed CraftHive projects for a new logo and wesbite.
We now require new business cards.
We hand out very little printed material to clients as all information is online. When we do hand out something, like a business card, we want it to have real impact and make a statement about the quality and professionalism of our company.
We have an idea of what we want our card to look like but we want a designer to make sure they have impact and look great.
Our requirements are…
Size: 85mm X 55mm - Landscape
Front of card: Logo plus the following contact information.
Dennis Marlow
Operations Manager
Phone +44(0) 1632 xxx xxx
Mobile +44(0) 7700 xxx xxx
Email denmo@korvantix.example
Address 17 Pellick Row, Aberdeen AB12 9QZ
Website www.korvantix.example
How you layout the front of the card is up to you, we would like to see some different ideas. Attached are two versions of our logo that may be used.
Back of card: We would like this to be simple but again have impact. Our current thought is to have the logo or just the large W design from the logo in white against a dark background, perhaps made up from the dark green in the logo.
The logos are attached so you can see the colours in them but the dark ones are..
Dark Blue = C:88, M:55, Y:44, K:28
Dark Green = C:87, M:53, Y:50, K:50
We sometimes also use a bright orange as an accent or highlight colour…
Orange: = C:0, M:39, Y:94, K:0

```html
<!DOCTYPE html>
<html lang="en">
<head>
<meta charset="utf-8">
<title>Korvantix Technologies – Business Cards</title>
<link rel="stylesheet" href="https://fonts.googleapis.com/css2?family=Open+Sans:wght@400;600;700;800&display=swap">
<style>
  :root {
    --backdrop: #7a5336;
    --card: #ffffff;
    --ink: #1f3e46;
    --ink-soft: #333b3e;
    --teal-dark: #15434b;
    --teal-mid: #3f6873;
    --teal-light: #9ab9bd;
    --mark: #4d7a83;
    --label: #1b130d;
  }
  * { margin: 0; padding: 0; box-sizing: border-box; }
  html, body { width: 1200px; height: 788px; overflow: hidden; }
  body {
    position: relative;
    background: var(--backdrop);
    font-family: "Open Sans", Arial, sans-serif;
  }
  .view-label {
    position: absolute;
    width: 503px;
    text-align: center;
    font-size: 21px;
    color: var(--label);
  }
  .card {
    position: absolute;
    width: 503px;
    height: 324px;
    border-radius: 22px;
    background: var(--card);
    overflow: hidden;
  }
  .card--dark { background: var(--teal-dark); }

  .brand {
    position: absolute;
    display: flex;
    align-items: center;
    gap: 14px;
    font-weight: 800;
    color: var(--ink);
    white-space: nowrap;
  }
  .brand__dot {
    border-radius: 50%;
    background: var(--mark);
    flex: none;
  }

  .name-band {
    position: absolute;
    left: 0; top: 172px;
    width: 431px; height: 35px;
    background: linear-gradient(90deg, var(--teal-mid), var(--teal-light));
    color: #fff;
    padding-left: 98px;
    line-height: 35px;
  }
  .name-band__name { font-weight: 700; font-size: 15px; }
  .name-band__role { font-size: 13px; font-weight: 400; }
  .band-block {
    position: absolute;
    left: 437px; top: 172px;
    width: 66px; height: 35px;
    background: var(--teal-dark);
  }

  .contact-list {
    position: absolute;
    left: 68px; top: 224px;
    list-style: none;
    font-size: 13px;
    color: var(--ink-soft);
  }
  .contact-list li {
    display: flex;
    align-items: center;
    gap: 6px;
    height: 22px;
  }
  .contact-list svg { width: 10px; height: 10px; fill: var(--ink-soft); flex: none; }
  .address {
    position: absolute;
    left: 291px; top: 271px;
    font-size: 13px;
    line-height: 19px;
    color: var(--ink-soft);
  }
  .web {
    position: absolute;
    left: 0; width: 100%;
    text-align: center;
    font-size: 18px;
    letter-spacing: 3.4px;
    color: var(--ink);
  }
</style>
</head>
<body>

  <div class="view-label" style="left:65px; top:18px;">Front</div>
  <div class="view-label" style="left:625px; top:18px;">Back - 1</div>
  <div class="view-label" style="left:65px; top:402px;">Back - 2</div>
  <div class="view-label" style="left:625px; top:402px;">Back - 3</div>

  <!-- Front -->
  <section class="card card--front" style="left:65px; top:55px;">
    <div class="brand" style="left:70px; top:62px; font-size:27px;">
      <span class="brand__dot" style="width:38px; height:38px;"></span>
      Korvantix Technologies
    </div>
    <div class="name-band">
      <span class="name-band__name">Dennis Marlow,</span>
      <span class="name-band__role">Operations Manager</span>
    </div>
    <div class="band-block"></div>
    <ul class="contact-list">
      <li><svg viewBox="0 0 10 10"><path d="M2 0.5 L3.8 2.8 L2.8 4 Q4 6.4 6 7.2 L7.2 6.2 L9.5 8 L8.2 9.5 Q2.5 8.5 0.5 1.8 Z"/></svg>+44(0) 1632 &nbsp;xxx xxx</li>
      <li><svg viewBox="0 0 10 10"><path d="M3 0 H7 Q8 0 8 1 V9 Q8 10 7 10 H3 Q2 10 2 9 V1 Q2 0 3 0 Z M3 1.5 V7.5 H7 V1.5 Z"/></svg>+44(0) 7700 xxx xxx</li>
      <li><svg viewBox="0 0 10 10"><path d="M0 2 H10 V8 H0 Z M1 3 L5 5.8 L9 3 V2.8 L5 5 L1 2.8 Z" fill-rule="evenodd"/></svg>denmo@korvantix.example</li>
      <li><svg viewBox="0 0 10 10"><circle cx="5" cy="5" r="4.5"/></svg>www.korvantix.example</li>
    </ul>
    <div class="address">17 Pellick Row<br>Aberdeen AB12 9QZ</div>
  </section>

  <!-- Back 1 -->
  <section class="card card--back" style="left:625px; top:55px;">
    <div class="brand" style="left:70px; top:112px; font-size:30px;">
      <span class="brand__dot" style="width:44px; height:44px;"></span>
      Korvantix Technologies
    </div>
    <div class="web" style="top:281px;">www.korvantix.example</div>
  </section>

  <!-- Back 2 -->
  <section class="card card--dark" style="left:65px; top:443px;">
    <div class="brand" style="left:0; width:100%; justify-content:center; top:130px; font-size:52px; color:var(--mark);">
      Korvantix
    </div>
  </section>

  <!-- Back 3 -->
  <section class="card card--back" style="left:625px; top:443px;">
    <span class="brand__dot" style="position:absolute; left:206px; top:36px; width:92px; height:92px;"></span>
    <div class="brand" style="left:0; width:100%; justify-content:center; top:172px; font-size:34px;">
      Korvantix Technologies
    </div>
    <div class="web" style="top:280px;">www.korvantix.example</div>
  </section>

</body>
</html>
```